Lotus Ridge Website

We need a website that has clean, asian looking images that relax and motivate people to come into our integrated medical center. My current website is www.needlecalmharbor.com and I would like the design for Lotus Ridge Wellness Partners to be similar but more inviting with video content and a product purchase store as well. A moving banner would be nice too. When people are looking for ways of losing weight or getting out of pain we want them to make the connection that we have the solution. This website needs to provide sufficient information so that patients are well informed and choose us as their health provider before they ever walk through our doors. We offer comprehensive natural medicine that is based on the principles that the body can heal itself when given the right conditions. Our services include medical weight loss and hormone balancing, acupuncture and chinese herbal medicine, physical medicine, trigger point injections, allergy testing and joint rehabilitation. The Medical Doctor and Licensed Acupuncturist work as a team to provide optimal care that is catered to each individual who comes through our doors.
Updates

Target Market(s)

40 to 50 year olds who want to lose weight or have pain issues.

Industry/Entity Type

Medical

Requirements
Must have
• Use photos from our website www.needlecalmharbor.com or similar content. Video content. Moving banner with relaxing images.
Nice to have
• Happy, healthy looking people. Medical Doctors working as a team. Friendly staff in a cutting edge facility.
Should not have
• Papyrus font, or big bold words.

```html
<!DOCTYPE html>
<html lang="en">
<head>
<meta charset="utf-8">
<title>Lotus Ridge Website</title>
<link rel="stylesheet" href="https://fonts.googleapis.com/css2?family=Roboto+Condensed:wght@400;700&display=swap">
<style>
:root{
  --olive:#6b6a2a;
  --pine:#2a4a3e;
  --pine-line:#5c7a6e;
  --ink:#1f1f1f;
  --muted:#444;
  --sage:#a9c8a0;
  --lime:#dfe4b8;
  --lime-deep:#c5d6a2;
  --sky:#dde7f3;
  --white:#ffffff;
  --rule:#d5d5d5;
}
*{margin:0;padding:0;box-sizing:border-box}
html,body{width:1130px;height:1200px;overflow:hidden;background:var(--white)}
body{position:relative;font-family:"Roboto Condensed",Arial,sans-serif;color:var(--ink)}
.site-header{position:absolute;left:13px;top:0;width:1104px;height:201px;border-right:1px solid var(--rule);border-bottom:1px solid var(--rule);box-shadow:0 2px 3px rgba(0,0,0,.08)}
.brand{position:absolute;left:8px;top:40px;width:140px;text-align:center}
.brand-mark{display:block;width:46px;height:46px;margin:0 auto 10px;background:var(--olive)}
.brand-name{font-size:17px;font-weight:700;color:var(--olive);line-height:1.2}
.main-nav{position:absolute;left:0;top:0;width:1104px;height:201px;list-style:none}
.main-nav li{position:absolute;top:168px;font-size:14px;line-height:16px;text-transform:uppercase;color:var(--ink);white-space:nowrap}
.main-nav li.active{top:132px;height:69px;width:114px;background:var(--pine);color:var(--white);text-align:center;padding-top:36px}
.dropdown{position:absolute;left:750px;top:199px;width:229px;height:215px;background:var(--pine);list-style:none;padding:16px 0 0 0;z-index:2}
.dropdown li{font-size:11.5px;font-weight:700;color:var(--white);text-transform:uppercase;height:22px;line-height:20px;padding-left:46px;border-bottom:1px solid var(--pine-line)}
.hero{position:absolute;left:13px;top:222px;width:1104px;height:386px}
.hero-copy{position:absolute;left:0;top:0;width:330px;height:386px;background:linear-gradient(180deg,var(--sky),#eef3fa 70%,#f6f8fc);padding:71px 0 0 31px;font-size:13.8px;line-height:26.5px}
.hero-copy strong{font-size:17.5px;font-weight:400}
.hero-photo{position:absolute;left:330px;top:0;width:774px;height:386px;background:linear-gradient(120deg,#c9d8ea 0%,#e9d2c2 45%,#f1ddd0 65%,#cfdcec 100%)}
.explainer{position:absolute;left:13px;top:613px;width:1104px;height:267px;background:var(--lime)}
.explainer h2{position:absolute;left:24px;top:40px;font-size:19px;font-weight:400;text-transform:uppercase}
.explainer p{position:absolute;left:24px;top:72px;width:630px;font-size:11.4px;line-height:26.5px}
.video-slot{position:absolute;left:765px;top:19px;width:298px;height:224px;background:var(--sage);display:flex;flex-direction:column;align-items:center;justify-content:center;gap:8px}
.video-slot span{font-size:14px;font-weight:700;text-transform:uppercase}
.feature{position:absolute;top:890px;height:222px;overflow:hidden}
.feature.pain{left:13px;width:558px;background:var(--sage)}
.feature.weight{left:571px;width:546px;background:var(--lime-deep)}
.feature-photo{position:absolute;top:0;height:222px}
.pain .feature-photo{left:320px;width:238px;background:linear-gradient(90deg,var(--sage),#b9b9b0 45%,#d7cfc8 80%,#e4a6a0)}
.weight .feature-photo{left:300px;width:246px;background:linear-gradient(90deg,var(--lime-deep),#9fb89a 40%,#d9b8a0 70%,#3a4a48)}
.feature h3{position:absolute;left:20px;top:41px;font-size:19px;font-weight:400;text-transform:uppercase;z-index:1;white-space:nowrap}
.feature p{position:absolute;left:20px;top:74px;width:340px;font-size:12px;font-weight:700;line-height:28.5px;z-index:1}
.learn-more{position:absolute;left:197px;top:183px;width:187px;height:27px;border-radius:14px;background:var(--white);font-size:11px;font-weight:700;text-transform:uppercase;line-height:27px;padding-left:23px;z-index:1}
.site-footer{position:absolute;left:21px;top:1136px;width:1096px}
.footer-links{font-size:11px;color:var(--muted)}
.copyright{position:absolute;top:26px;font-size:11px;color:var(--muted);white-space:nowrap}
.social{position:absolute;right:0;top:-2px;display:flex;gap:4px}
.social span{width:26px;height:26px;border-radius:4px;background:var(--pine)}
</style>
</head>
<body>
<header class="site-header">
  <div class="brand"><span class="brand-mark"></span><div class="brand-name">Lotus Ridge Acupuncture</div></div>
  <ul class="main-nav">
    <li style="left:163px">Ren Kaito</li>
    <li style="left:274px">Seitai Shinpo</li>
    <li style="left:408px">Acupuncture</li>
    <li style="left:547px">Biography</li>
    <li style="left:665px">Nutrition</li>
    <li class="active" style="left:751px">Services</li>
    <li style="left:888px">My Journey</li>
    <li style="left:1016px">Contact Us</li>
  </ul>
</header>
<ul class="dropdown">
  <li>Medical Weight Loss</li>
  <li>Hormone Balancing</li>
  <li>Acupuncture</li>
  <li>Chinese Herbal Medicine</li>
  <li>Physical Medicine</li>
  <li>Trigger Point Injections</li>
  <li>Allergy Testing</li>
  <li>Joint Rehabilitation</li>
</ul>
<section class="hero">
  <div class="hero-copy">&nbsp;At <strong>Lotus Ridge Acupuncture</strong> the system of acupuncture used is called Seitai Shinpo (which translates into “correct posture acupuncture method”) that uses acupuncture and moxibustion to balance structural distortions by releasing tense areas of contraction along the spine.&nbsp; When the structure is properly balanced then the body will heal much quicker.</div>
  <div class="hero-photo" role="img" aria-label="Photo of a relaxed patient resting during an acupuncture treatment"></div>
</section>
<section class="explainer">
  <h2>How does acupuncture work?</h2>
  <p>As the needles are carefully inserted into acupuncture points, specific cells stimulate nerve pathways that trigger a healing response to a particular organ system or area of the body.&nbsp; Acupuncture also acts on the autonomic nervous system and causes the release of endorphins, enkephalins and other natural pain relieving chemicals.&nbsp; At Lotus Ridge Acupuncture the system of acupuncture used is called Seitai Shinpo (which translates into "correct posture acupuncture method") that uses acupuncture and moxibustion to balance structural distortions by releasing tense areas of contraction along the spine.&nbsp; When the structure is properly balanced then the body will heal much quicker.</p>
  <div class="video-slot">
    <svg width="40" height="40" viewBox="0 0 40 40" aria-hidden="true"><circle cx="19" cy="19" r="16" fill="#e8efe4"/><circle cx="19" cy="11" r="4" fill="#a9c8a0"/><circle cx="19" cy="27" r="4" fill="#a9c8a0"/><circle cx="11" cy="19" r="4" fill="#a9c8a0"/><circle cx="27" cy="19" r="4" fill="#a9c8a0"/><path d="M30 30 L38 36" stroke="#e8efe4" stroke-width="4"/></svg>
    <span>Video Space</span>
  </div>
</section>
<section class="feature pain">
  <div class="feature-photo" role="img" aria-label="Photo of a person holding their lower back in pain"></div>
  <h3>What can be treated with acupuncture?</h3>
  <p>Acupuncture has been used to effectively treat numerous health conditions for thousands of years.&nbsp; According to the Global Wellness Council, ¼ of the earth's population receives acupuncture treatment on a continual basis.</p>
  <div class="learn-more">Learn More</div>
</section>
<section class="feature weight">
  <div class="feature-photo" role="img" aria-label="Photo of a slim waist being measured with a tape measure"></div>
  <h3>What can be treated with acupuncture?</h3>
  <p>Acupuncture has been used to effectively treat numerous health conditions for thousands of years.&nbsp; According to the Global Wellness Council, ¼ of the earth's population receives acupuncture treatment on a continual basis.</p>
  <div class="learn-more">Learn More</div>
</section>
<footer class="site-footer">
  <div class="footer-links">Ren Kaito · Seitai Shinpo · Acupuncture · Biography · Nutrition · My Journey · Contact Us ·</div>
  <div class="copyright">Copyright 2007© Lotus Ridge Acupuncture — All Rights Reserved</div>
  <div class="social" aria-label="Social links"><span></span><span></span><span></span><span></span></div>
</footer>
</body>
</html>
```